Business Card Design for Flood Rescue 360 - Property Restoration Professionals

I need a business card designed for Flood Rescue 360. We are a full-service property restoration solution. Providing water, fire, smoke & storm restoration as well as mold remediation and full remodel or reconstruction to homes and businesses across Dallas-Fort Worth, TX.
Target Market(s)
home and business owners with insurance covered property damage from water, fire or storm related damage
Industry/Entity Type
property restoration
Contact Information for Business Card
Marcus Pelley General Manager Cell: 214-555-0193 Office: 469-555-0148 email: Marcus@FloodRescue360.example services: Water, Fire, Mold, Reconstruction Tagline: Urgency for Your Water Emergency!
Look and feel
Each slider illustrates characteristics of the customer's brand and the style your logo design should communicate.

```html
<!DOCTYPE html>
<html lang="en">
<head>
<meta charset="utf-8">
<title>Flood Rescue 360 – Business Card</title>
<link href="https://fonts.googleapis.com/css2?family=Montserrat:wght@400;500;700&display=swap" rel="stylesheet">
<style>
  :root{
    --brand-blue:#00aee6;
    --brand-blue-deep:#0096c7;
    --brand-blue-light:#3cc3ee;
    --ink:#1a1a1a;
    --paper:#ffffff;
    --stage:#eceae8;
  }
  *{box-sizing:border-box;margin:0;padding:0}
  html,body{width:1200px;height:768px;overflow:hidden}
  body{background:var(--stage);font-family:"Montserrat",sans-serif;display:flex;align-items:center;justify-content:center;gap:48px}
  .card{width:540px;height:309px;position:relative;overflow:hidden;box-shadow:0 10px 28px rgba(0,0,0,.14)}

  /* Front */
  .card-front{background:var(--paper)}
  .brand{position:absolute;left:44px;top:62px;right:44px;display:flex;align-items:center;justify-content:space-between}
  .brand-name{color:var(--brand-blue);font-weight:700;font-size:32px;line-height:1.1}
  .brand-dot{width:72px;height:72px;border-radius:50%;background:var(--brand-blue);flex:none}
  .person{position:absolute;left:44px;top:172px}
  .person-name{color:var(--brand-blue);font-weight:700;font-size:19px;line-height:1.2}
  .person-title{color:var(--ink);font-size:12px;margin-top:3px}
  .divider{position:absolute;left:222px;top:172px;width:1.5px;height:56px;background:var(--brand-blue)}
  .contacts{position:absolute;left:236px;top:172px;list-style:none;font-size:12px;color:var(--ink);line-height:19px}
  .contacts li{display:flex;align-items:center;gap:7px}
  .contacts svg{width:11px;height:11px;fill:var(--brand-blue);flex:none}
  .services{position:absolute;left:0;right:0;top:246px;text-align:center}
  .services-label{color:var(--brand-blue);font-weight:700;font-size:12px;text-decoration:underline;text-underline-offset:3px}
  .services-row{display:flex;align-items:center;gap:10px;margin-top:6px}
  .services-row .rule{flex:1;height:1.5px;background:var(--brand-blue)}
  .services-list{font-weight:700;font-size:12px;color:var(--ink);white-space:nowrap}
  .services-list b{color:var(--brand-blue)}

  /* Back */
  .card-back{background:var(--brand-blue)}
  .pattern{position:absolute;inset:0;background:linear-gradient(160deg,var(--brand-blue-light) 0%,var(--brand-blue) 45%,var(--brand-blue-deep) 100%)}
  .tagline{position:absolute;right:40px;bottom:70px;color:var(--paper);font-weight:700;font-size:15px}
  .back-brand{position:absolute;right:40px;bottom:28px;display:flex;align-items:center;gap:7px;color:var(--paper);font-weight:700;font-size:13px}
  .back-brand .dot{width:14px;height:14px;border-radius:50%;background:var(--paper)}
</style>
</head>
<body>
  <section class="card card-front">
    <div class="brand">
      <div class="brand-name">Flood Rescue 360</div>
      <div class="brand-dot"></div>
    </div>
    <div class="person">
      <div class="person-name">Marcus Pelley</div>
      <div class="person-title">General Manager</div>
    </div>
    <div class="divider"></div>
    <ul class="contacts">
      <li><svg viewBox="0 0 24 24"><path d="M6.6 10.8a15.1 15.1 0 0 0 6.6 6.6l2.2-2.2c.3-.3.7-.4 1-.2 1.1.4 2.3.6 3.6.6.6 0 1 .4 1 1V20c0 .6-.4 1-1 1A17 17 0 0 1 3 4c0-.6.4-1 1-1h3.5c.6 0 1 .4 1 1 0 1.3.2 2.5.6 3.6.1.3 0 .7-.2 1z"/></svg>214-555-0193</li>
      <li><svg viewBox="0 0 24 24"><path d="M3 8c3-4 15-4 18 0v3h-5V9H8v2H3zM6 13h12l2 7H4zm6 1.5a2.5 2.5 0 1 0 0 5 2.5 2.5 0 0 0 0-5z"/></svg>469-555-0148</li>
      <li><svg viewBox="0 0 24 24"><path d="M2 5h20v14H2zm2 2v.5l8 5 8-5V7z"/></svg>Marcus@FloodRescue360.example</li>
    </ul>
    <div class="services">
      <div class="services-label">Our Services</div>
      <div class="services-row">
        <span class="rule"></span>
        <span class="services-list"><b>•</b> Water <b>•</b> Fire <b>•</b> Mold <b>•</b> Reconstruction</span>
        <span class="rule"></span>
      </div>
    </div>
  </section>

  <section class="card card-back">
    <div class="pattern" role="img" aria-label="Repeating tonal blue pattern of the brand symbol"></div>
    <div class="tagline">Urgency for Your Water Emergency!</div>
    <div class="back-brand"><span class="dot"></span>Flood Rescue 360</div>
  </section>
</body>
</html>
```